Coastal Learner Bureau business cards

Australian company about to start offering its services. We recruit international students to come to study English, vocational education and postgraduate courses in Australia. We help them find the institution and select the right city they want to come to Australia. We are a young, online oriented and supportive agency. Our clients are between 18 and 35 years old, mainly University students, young professionals or people with work experience. We provide much more information that any other agency offer. We administrate a Facebook group with more than 11.000 members that daily ask questions about general information when coming to Australia, while they are here and even after they leave the country

Target Market(s)

International students from South America, Central America and Europe

Industry/Entity Type

Student

Contact Information for Business Card

Tomas Bilbrea
Managing Director
tomas@kelvarin.com.au
www.kelvoria.com.au
+61 491058264
Melbourne, Australia

Font styles to use
Serif
Sans Serif

Colors

Designer to choose colors to be used in the design.

Requirements
Must have
• Horizontal design
• Standard business card size and shape. If font uses green or yellow colours, they will have to match the ones from the logo
Nice to have
• UPDATE: Use the contents of the green image to design one of the card sides. Use our logo in the background of that side as watermark.
• Passport image, or immigration stamps. A picture of the Yarra River (from Melbourne) would be cool as well.
Should not have
• Non-standard business card size and shape
• Not black as the background colour of any sides as we are not a VIP agency or a hight class service. We are orientes to young people and they like colours, pictures, something attractive.
• Vertical design
• NO YELLOW or BLACK AS THE BACKGROUND COLOUR OF ANY SIDE OF THE BIZ CARD

```html
<!DOCTYPE html>
<html lang="en">
<head>
<meta charset="utf-8">
<title>Kelvoria business cards</title>
<link rel="stylesheet" href="https://fonts.googleapis.com/css2?family=Open+Sans:wght@400;600;700&display=swap">
<style>
  :root {
    --brand-green: #0e6b3d;
    --brand-green-dark: #0a5a33;
    --brand-green-light: #1b8d58;
    --brand-yellow: #e3b51f;
    --card-white: #f4f4f2;
    --ink-grey: #5c5c5c;
    --backdrop: #d9dbd8;
  }
  * { margin: 0; padding: 0; box-sizing: border-box; }
  html, body {
    width: 1200px;
    height: 900px;
    overflow: hidden;
    background: var(--backdrop);
    font-family: "Open Sans", Arial, sans-serif;
  }
  .sheet {
    width: 1200px;
    height: 900px;
    display: flex;
    flex-direction: column;
    align-items: center;
    justify-content: center;
    gap: 40px;
  }
  .card {
    position: relative;
    width: 680px;
    height: 388px;
    border-radius: 4px;
    overflow: hidden;
    box-shadow: 0 6px 18px rgba(0,0,0,0.18);
  }

  /* Front side */
  .card-front {
    background: linear-gradient(135deg, var(--brand-green-light) 0%, var(--brand-green) 45%, var(--brand-green-dark) 100%);
    color: #ffffff;
  }
  .card-front .brand-name {
    position: absolute;
    top: 120px;
    left: 0;
    width: 100%;
    text-align: center;
    font-size: 68px;
    font-weight: 700;
    letter-spacing: 1px;
    color: #ffffff;
  }
  .card-front .tagline-row {
    position: absolute;
    top: 272px;
    left: 0;
    width: 100%;
    display: flex;
    align-items: center;
    justify-content: center;
    gap: 12px;
  }
  .tagline-rule {
    height: 1px;
    width: 180px;
    background: rgba(255,255,255,0.55);
  }
  .tagline {
    font-size: 15px;
    font-weight: 600;
    color: #ffffff;
    white-space: nowrap;
  }

  /* Back side */
  .card-back {
    background: var(--card-white);
  }
  .card-back .brand-name {
    position: absolute;
    top: 62px;
    left: 0;
    width: 100%;
    text-align: center;
    font-size: 60px;
    font-weight: 700;
    letter-spacing: 1px;
    color: var(--brand-green);
  }
  .contact-list {
    position: absolute;
    right: 36px;
    top: 178px;
    list-style: none;
    text-align: right;
  }
  .contact-list li {
    display: flex;
    align-items: center;
    justify-content: flex-end;
    gap: 8px;
    font-size: 14px;
    line-height: 24px;
    color: var(--ink-grey);
  }
  .contact-icon {
    width: 14px;
    height: 14px;
    flex: none;
  }
  .divider {
    position: absolute;
    top: 262px;
    left: 40px;
    right: 36px;
    height: 5px;
    display: flex;
    align-items: center;
  }
  .divider-accent {
    width: 170px;
    height: 5px;
    background: var(--brand-green);
  }
  .divider-line {
    flex: 1;
    height: 1px;
    background: var(--brand-yellow);
  }
  .holder {
    position: absolute;
    left: 40px;
    top: 278px;
  }
  .holder-name {
    font-size: 19px;
    font-weight: 700;
    color: var(--brand-green);
    text-transform: uppercase;
    line-height: 24px;
  }
  .holder-role {
    font-size: 17px;
    font-weight: 400;
    color: var(--brand-yellow);
    text-transform: uppercase;
    line-height: 22px;
  }
  .holder-location {
    font-size: 15px;
    color: var(--ink-grey);
    line-height: 26px;
  }
</style>
</head>
<body>
<main class="sheet">
  <section class="card card-front" aria-label="Card front">
    <div class="brand-name">Kelvoria</div>
    <div class="tagline-row">
      <span class="tagline-rule"></span>
      <span class="tagline">Hacemos más por ti!</span>
      <span class="tagline-rule"></span>
    </div>
  </section>

  <section class="card card-back" aria-label="Card back">
    <div class="brand-name">Kelvoria</div>

    <ul class="contact-list">
      <li>+61 491058264
        <svg class="contact-icon" viewBox="0 0 14 14" aria-hidden="true">
          <circle cx="7" cy="7" r="7" fill="var(--brand-green)"/>
          <path d="M4.3 3.6c.4-.3.8-.2 1 .1l.7 1.1c.2.3.1.6-.1.8l-.4.3c.3.8 1 1.6 1.9 2l.3-.4c.2-.2.5-.3.8-.1l1.1.7c.3.2.4.6.1 1-.5.7-1.2.9-2 .6-1.7-.6-3-1.9-3.6-3.6-.3-.8-.1-1.6.2-2.5z" fill="#fff"/>
        </svg>
      </li>
      <li>tomas@kelvarin.com.au
        <svg class="contact-icon" viewBox="0 0 14 14" aria-hidden="true">
          <circle cx="7" cy="7" r="7" fill="var(--brand-green)"/>
          <rect x="3.5" y="4.5" width="7" height="5" fill="#fff"/>
          <path d="M3.5 4.5L7 7.3l3.5-2.8" fill="none" stroke="var(--brand-green)" stroke-width="0.8"/>
        </svg>
      </li>
      <li>www.kelvoria.com.au
        <svg class="contact-icon" viewBox="0 0 14 14" aria-hidden="true">
          <circle cx="7" cy="7" r="7" fill="var(--brand-green)"/>
          <circle cx="7" cy="7" r="3.6" fill="none" stroke="#fff" stroke-width="0.9"/>
          <ellipse cx="7" cy="7" rx="1.5" ry="3.6" fill="none" stroke="#fff" stroke-width="0.8"/>
          <line x1="3.4" y1="7" x2="10.6" y2="7" stroke="#fff" stroke-width="0.8"/>
        </svg>
      </li>
    </ul>

    <div class="divider">
      <span class="divider-accent"></span>
      <span class="divider-line"></span>
    </div>

    <div class="holder">
      <p class="holder-name">Tomas Bilbrea</p>
      <p class="holder-role">Managing Director</p>
      <p class="holder-location">Melbourne, Australia</p>
    </div>
  </section>
</main>
</body>
</html>
```